Using attached logo that has been created

Business card with logo that's attached. Maybe with water or the cartoon van in background. Looking for it to not be so plain and not too white.
Information to include;
Rodney Ashcombe
(555) 218-7730
Info@bramleypipeworks.example
www.bramleypipeworks.example
License # 4627195
Looking forward to the designs u come up with.
Thank you!
-Delphine
Target Market(s)
Plumbing
Industry/Entity Type
Plumbing
Contact Information for Business Card
Listed above

```html
<!DOCTYPE html>
<html lang="en">
<head>
<meta charset="UTF-8">
<title>Bramley Pipeworks – Business Card</title>
<link href="https://fonts.googleapis.com/css2?family=Roboto:wght@400;500;700&display=swap" rel="stylesheet">
<style>
  :root {
    --bg: #d4d4d4;
    --card-white: #ffffff;
    --brand-blue: #1a56b8;
    --brand-yellow: #f2b81c;
    --text-grey: #4a4a4a;
    --water-light: #f4eee2;
    --water-mid: #e6d6b6;
    --water-deep: #d9bd8c;
    --figure-blue: #2a5fbf;
    --figure-tan: #9c8664;
    --van-white: #e8ecef;
    --van-dark: #3b4758;
  }
  * { box-sizing: border-box; margin: 0; padding: 0; }
  html, body { width: 1200px; height: 800px; overflow: hidden; }
  body {
    background: var(--bg);
    font-family: "Roboto", Arial, sans-serif;
    position: relative;
  }
  .card {
    position: absolute;
    top: 250px;
    width: 525px;
    height: 300px;
    border-bottom: 4px solid var(--brand-yellow);
    box-shadow: 0 12px 28px rgba(0,0,0,0.22);
    overflow: hidden;
  }
  .card--front { left: 50px; background: var(--card-white); }
  .card--back { left: 625px; }

  .mascot {
    position: absolute;
    border-radius: 40% 40% 14px 14px;
    background: linear-gradient(180deg, var(--figure-blue) 0 45%, var(--figure-tan) 45% 100%);
    opacity: 0.85;
  }
  .brand-name {
    position: absolute;
    font-weight: 700;
    color: var(--brand-blue);
    text-transform: uppercase;
    display: flex;
    align-items: center;
    gap: 8px;
    white-space: nowrap;
    line-height: 1;
  }
  .brand-name .brand-dot {
    width: 10px; height: 10px; border-radius: 50%;
    background: var(--brand-yellow);
    flex: none;
  }

  /* Front */
  .card--front .mascot { left: 78px; top: 62px; width: 100px; height: 138px; }
  .card--front .brand-name { left: 36px; top: 212px; font-size: 20px; }
  .license {
    position: absolute; left: 36px; bottom: 20px;
    font-size: 15px; color: var(--brand-blue);
  }
  .license .license-number { color: var(--brand-yellow); }

  .contact-block { position: absolute; left: 262px; top: 38px; }
  .person-name {
    font-size: 22px; font-weight: 500; color: var(--brand-blue);
    letter-spacing: 0.5px; margin-bottom: 10px;
  }
  .contact-list { list-style: none; }
  .contact-list li {
    display: flex; align-items: center; gap: 7px;
    font-size: 12.5px; color: var(--text-grey); line-height: 19px;
  }
  .contact-list svg { width: 12px; height: 12px; flex: none; }

  .van {
    position: absolute; right: 18px; bottom: 24px;
    width: 220px; height: 120px;
    border-radius: 40px 60px 16px 16px;
    background: linear-gradient(180deg, var(--van-white) 0 75%, var(--van-dark) 75% 100%);
  }

  /* Back */
  .water-surface {
    position: absolute; inset: 0;
    background:
      radial-gradient(ellipse at 75% 20%, var(--water-light) 0%, rgba(244,238,226,0) 60%),
      linear-gradient(160deg, var(--water-mid) 0%, var(--water-mid) 45%, var(--water-deep) 100%);
  }
  .card--back .mascot { left: 208px; top: 28px; width: 110px; height: 170px; }
  .card--back .brand-name {
    left: 0; right: 0; justify-content: center;
    top: 216px; font-size: 30px;
  }
</style>
</head>
<body>

<section class="card card--front">
  <div class="mascot" role="img" aria-label="Cartoon plumber mascot holding a pipe wrench and circular saw"></div>
  <div class="brand-name"><span class="brand-dot"></span>Bramley Pipeworks</div>

  <div class="contact-block">
    <h1 class="person-name">RODNEY ASHCOMBE</h1>
    <ul class="contact-list">
      <li>
        <svg viewBox="0 0 24 24"><path fill="#1a56b8" d="M6.6 10.8a15 15 0 0 0 6.6 6.6l2.2-2.2c.3-.3.7-.4 1-.2 1.1.4 2.3.6 3.6.6.6 0 1 .4 1 1V20c0 .6-.4 1-1 1A17 17 0 0 1 3 4c0-.6.4-1 1-1h3.5c.6 0 1 .4 1 1 0 1.3.2 2.5.6 3.6.1.3 0 .7-.2 1z"/></svg>
        (555) 218-7730
      </li>
      <li>
        <svg viewBox="0 0 24 24"><rect x="2" y="5" width="20" height="14" rx="1" fill="#1a56b8"/><path d="M2 6l10 7 10-7" stroke="#fff" stroke-width="1.6" fill="none"/></svg>
        Info@bramleypipeworks.example
      </li>
      <li>
        <svg viewBox="0 0 24 24"><circle cx="12" cy="12" r="10" fill="#1a56b8"/><path d="M2 12h20M12 2c3 3 3 17 0 20M12 2c-3 3-3 17 0 20" stroke="#fff" stroke-width="1.4" fill="none"/></svg>
        www.bramleypipeworks.example
      </li>
    </ul>
  </div>

  <div class="van" role="img" aria-label="Cartoon plumber waving a wrench from a white work van"></div>

  <p class="license">License # <span class="license-number">4627195</span></p>
</section>

<section class="card card--back">
  <div class="water-surface" role="img" aria-label="Photograph of water droplets beading on a warm beige surface"></div>
  <div class="mascot" role="img" aria-label="Cartoon plumber mascot holding a pipe wrench and circular saw"></div>
  <div class="brand-name"><span class="brand-dot"></span>Bramley Pipeworks</div>
</section>

</body>
</html>
```